BRTL web site redesign

Coastal Linkage Engineering service (BRTL) is a diverse technology company specialising in design and installation of fibre optics, network convergence and building services, for commercial clients in Australia, we required a new design of our website to attract new clients, generate sales leads, and provide information about our services to the market. The site and should have a new technology look and feel and be designed in word press. our branding colour is blue.

Target Market(s)

New developments, Construction organisations, Commercial end users, IT managers, Consultants.

Industry/Entity Type

It Company

Number of Pages Required

5+ page

Font styles to use
Sans Serif

Colors
0292cd
3176b5

Requirements
Must have
• key pages.
• Home page with some sizzle, automated pictures running through, I like the look of this competitor website http://www.gleamwirex.com.au/ good clean menus and easy to navigate.
• Services page our key services are Fibre optics, Security, Building services,Electrical. I would like the same page layout (Design) for all our services, with a find out more link on each page, manly picture driven with text around our key messaging.
• About us page with space for company profile and directors pictures, bio and contact information.
• Certifications / Accreditations page with have over 20 certifications on different products from suppliers, and a number of licences from governing bodies.
• Current and past projects page with case studies and customer outcomes
• Contact us page with options around what services they require more information on, please keep in mind the site is around generating sales Leeds and being seen as an industry expert.
Nice to have
• RSS feeds, Linked in link, to be placed within the design, Consistent BRTL branding,Same colour blue as our logo Document library for education information, white papers, presentations etc,
• a new technology look and feel, mobile friendly.
Should not have
• boring layout, move away from our cuurent website http://www.brtlgroup.com.au/
• no e eCommerce store required.

```html
<!DOCTYPE html>
<html lang="en">
<head>
<meta charset="utf-8">
<title>BRTL – Coastal Linkage Engineering service</title>
<link href="https://fonts.googleapis.com/css2?family=Open+Sans:wght@400;600;700&family=Oswald:wght@400;500&display=swap" rel="stylesheet">
<style>
:root{
  --brand:#0292cd;
  --brand-deep:#3176b5;
  --page:#e6e8ea;
  --panel:#ffffff;
  --ink:#333b44;
  --muted:#7a828a;
  --rule:#dfe3e6;
  --footer:#3b3e42;
  --footer-deep:#2a2c2f;
  --footer-text:#b9bec3;
}
*{box-sizing:border-box;margin:0;padding:0}
html,body{width:1200px;height:2704px;overflow:hidden}
body{background:var(--page);font-family:"Open Sans",Arial,sans-serif;color:var(--ink);font-size:12px;line-height:1.5}
.site{position:relative;width:1200px;height:2704px}
.sheet{position:absolute;left:180px;top:0;width:840px;height:2704px;background:var(--panel);box-shadow:0 0 10px rgba(0,0,0,.08)}
.block{position:absolute;left:0;width:840px}
a{color:inherit;text-decoration:none}
.btn{display:inline-block;background:var(--brand);color:#fff;font-size:10px;font-weight:600;padding:5px 14px;border-radius:2px}

/* header */
.header{top:0;height:136px}
.brand{position:absolute;left:20px;top:26px;display:flex;align-items:center;gap:10px}
.brand-mark{width:36px;height:36px;background:var(--brand)}
.brand-name{font-size:40px;font-weight:700;color:var(--brand);letter-spacing:1px;line-height:1}
.brand-tag{position:absolute;left:20px;top:72px;font-size:9px;color:var(--muted)}
.account-links{position:absolute;right:20px;top:0;display:flex;gap:8px}
.account-links a{background:var(--footer);color:#fff;font-size:9px;font-weight:600;padding:4px 12px}
.phone{position:absolute;left:350px;top:80px;display:flex;align-items:center;gap:8px;font-size:22px;font-weight:700;color:var(--ink)}
.search{position:absolute;left:520px;top:84px;display:flex}
.search span{width:210px;height:26px;border:1px solid var(--rule);font-size:10px;color:var(--muted);padding:5px 8px}
.search b{background:var(--brand);color:#fff;font-size:10px;padding:6px 14px}

/* nav */
.nav{top:136px;height:30px;background:var(--brand);display:flex;padding-left:10px}
.nav a{color:#fff;font-size:11px;font-weight:600;padding:0 24px;line-height:30px;border-right:1px solid rgba(255,255,255,.25)}
.nav a.current{background:var(--brand-deep)}

/* slider */
.slider{top:176px;height:344px;left:20px;width:800px;background:linear-gradient(135deg,#5d7381 0%,#9fb4c2 45%,#3a8fb7 100%)}
.slider-caption{position:absolute;left:0;right:0;top:236px;background:rgba(20,40,55,.55);color:#fff;font-family:"Oswald",sans-serif;font-size:24px;letter-spacing:.5px;padding:8px 30px}
.slider-arrow{position:absolute;top:150px;width:24px;height:40px;background:rgba(0,0,0,.45)}
.slider-dots{position:absolute;left:0;right:0;bottom:10px;display:flex;justify-content:center;gap:6px}
.slider-dots i{width:9px;height:9px;border-radius:50%;background:#fff;opacity:.6}
.slider-dots i.on{background:var(--brand);opacity:1}

/* features */
.features{top:544px;height:250px;display:flex;padding:0 20px;gap:20px}
.feature{flex:1;border:1px solid var(--rule);padding:10px 14px;text-align:center;position:relative}
.feature h3{display:flex;align-items:center;gap:8px;font-size:12px;font-weight:700;color:var(--brand);border-bottom:1px solid var(--rule);padding-bottom:8px;margin-bottom:12px}
.feature p{font-size:10px;color:var(--muted);margin-bottom:14px}
.feature ul{list-style:none;text-align:left;font-size:10px;color:var(--ink)}
.feature li{border-bottom:1px solid var(--rule);padding:5px 0}
.feature .btn{position:absolute;left:50%;transform:translateX(-50%);bottom:14px}

/* welcome */
.welcome{top:850px;height:170px;padding:0 20px}
.welcome h2{font-size:24px;font-weight:600;color:var(--ink);margin-bottom:10px}
.welcome h2 span{color:var(--brand)}
.welcome p{width:590px;font-size:10px;color:var(--muted)}
.welcome .more{display:block;width:590px;text-align:right;color:var(--brand);font-size:10px;margin-top:6px}
.welcome-photo{position:absolute;right:20px;top:0;width:160px;height:120px;background:linear-gradient(135deg,#8fb3cc,#d9e5ee)}

/* tabs */
.showcase{top:1046px;height:200px;padding:0 20px}
.tabs{display:flex}
.tabs span{font-size:11px;font-weight:600;padding:8px 24px;background:#f1f3f5;color:var(--ink);border:1px solid var(--rule);border-bottom:none}
.tabs span.on{background:var(--brand);color:#fff}
.tab-panel{background:var(--brand);height:160px;display:flex;align-items:center;justify-content:space-around;padding:0 20px}
.thumb{width:128px;height:96px;border:4px solid #fff}

/* about */
.about{top:1284px;height:400px;padding:0 20px}
.about-copy{position:absolute;left:20px;top:0;width:520px;text-align:center}
.about-copy h2{font-size:20px;font-weight:600;border-bottom:1px solid var(--rule);padding-bottom:6px;margin-bottom:12px}
.about-copy p{font-size:10px;color:var(--muted);width:300px;margin:0 auto 8px}
.news{position:absolute;right:20px;top:20px;width:260px;border:1px solid var(--rule)}
.news h4{background:var(--brand);color:#fff;font-size:10px;font-weight:700;padding:6px 10px}
.news-item{display:flex;gap:8px;padding:8px 10px;border-bottom:1px solid var(--rule)}
.news-item i{flex:none;width:40px;height:32px;background:linear-gradient(135deg,#6f95b0,#c9d9e4)}
.news-item b{display:block;color:var(--brand);font-size:9px}
.news-item span{font-size:9px;color:var(--muted);line-height:1.3}
.news .all{display:block;text-align:right;font-size:9px;color:#d04a2a;padding:6px 10px}

/* partners */
.partners{top:1716px;height:170px;text-align:center}
.section-title{font-size:22px;font-weight:600;color:var(--ink)}
.section-sub{font-size:10px;color:var(--muted);margin:4px 0 24px}
.partner-row{display:flex;justify-content:center;gap:24px}
.partner-row i{width:120px;height:46px;background:#cfd4d8;border-radius:3px}

/* testimonials */
.testimonials{top:1926px;height:340px;padding:0 20px}
.testimonials h2{font-size:22px;font-weight:600;margin-bottom:24px}
.quotes{display:grid;grid-template-columns:1fr 1fr;gap:40px 40px}
.quote{display:flex;gap:14px}
.quote .avatar{flex:none;width:56px;height:56px;border-radius:50%;background:linear-gradient(135deg,#aab8c4,#dde4ea)}
.quote p{font-size:10px;color:var(--muted)}
.quote cite{display:block;font-style:normal;font-size:10px;margin-top:6px;color:var(--ink)}
.quote cite b{color:#d04a2a;font-weight:600}

/* footer */
.footer{top:2290px;height:244px;background:var(--footer);display:flex;padding:24px 20px;gap:20px}
.footer-col{flex:1}
.footer-col h5{color:#fff;font-size:10px;font-weight:700;border-bottom:1px solid #55595e;padding-bottom:6px;margin-bottom:8px}
.footer-col li{list-style:none;color:var(--footer-text);font-size:10px;line-height:1.9}
.footer-col.split ul{columns:2}
.newsletter{top:2534px;height:86px;background:var(--footer-deep);text-align:center;padding-top:14px}
.newsletter-row{display:flex;justify-content:center;align-items:center;gap:14px}
.newsletter h5{font-family:"Oswald",sans-serif;color:#fff;font-size:22px;font-weight:400;letter-spacing:1px}
.newsletter-note{color:var(--footer-text);font-size:9px;text-align:left}
.newsletter .field{width:180px;height:22px;background:#fff;font-size:9px;color:var(--muted);padding:4px 8px;text-align:left}
.newsletter .btn{padding:4px 16px}
.follow{display:flex;justify-content:center;align-items:center;gap:6px;margin-top:10px;color:var(--footer-text);font-size:9px}
.follow i{width:14px;height:14px;border-radius:50%;background:#5e6368}
.copyright{top:2620px;height:84px;background:var(--footer-deep);border-top:1px solid #3f4246;text-align:center;color:var(--footer-text);font-size:9px;padding-top:12px}
</style>
</head>
<body>
<div class="site">
  <div class="sheet">

    <header class="block header">
      <div class="brand"><span class="brand-mark"></span><span class="brand-name">BRTL</span></div>
      <div class="brand-tag">Coastal Linkage Engineering service</div>
      <nav class="account-links"><a href="#">MY ACCOUNT</a><a href="#">MY CART</a></nav>
      <div class="phone">
        <svg width="22" height="22" viewBox="0 0 24 24"><path d="M6.6 10.8a15 15 0 006.6 6.6l2.2-2.2a1 1 0 011-.25 11.4 11.4 0 003.6.57 1 1 0 011 1V20a1 1 0 01-1 1A17 17 0 013 4a1 1 0 011-1h3.5a1 1 0 011 1c0 1.25.2 2.45.57 3.57a1 1 0 01-.25 1z" fill="#333b44"/></svg>
        1300 555 019
      </div>
      <div class="search"><span>Search</span><b>Search</b></div>
    </header>

    <nav class="block nav">
      <a class="current" href="#">HOME</a><a href="#">ABOUT US</a><a href="#">SERVICES</a><a href="#">ISP</a><a href="#">RECENT PROJECTS</a><a href="#">BLOG</a><a href="#">CONTACT US</a>
    </nav>

    <section class="block slider" role="img" aria-label="Rotating photo of technicians working on fibre optic network cabling">
      <span class="slider-arrow" style="left:0"></span>
      <span class="slider-arrow" style="right:0"></span>
      <div class="slider-caption">LORM IPSUM DOLOR SIT AMET, CONSECTETUR ADIPISCING</div>
      <div class="slider-dots"><i></i><i class="on"></i><i></i><i></i></div>
    </section>

    <section class="block features">
      <article class="feature">
        <h3><svg width="18" height="18" viewBox="0 0 20 20"><circle cx="10" cy="7" r="4" fill="#0292cd"/><path d="M2 19a8 8 0 0116 0z" fill="#0292cd"/></svg>WHO WE ARE</h3>
        <p>Lorem ipsum dolor sit amet, consectetur adipiscing elit. Sed diam nonummy in convallis gravida lacus. Mauris metus accumsan, aliquam et eleifend. Sollicitudin sed massa vel enim eu. Curabitur tempus vehicula nisi ut porttitor in convallis.</p>
        <a class="btn" href="#">Read more</a>
      </article>
      <article class="feature">
        <h3><svg width="18" height="18" viewBox="0 0 20 20"><rect x="2" y="4" width="16" height="11" rx="1" fill="none" stroke="#0292cd" stroke-width="2"/><rect x="7" y="16" width="6" height="2" fill="#0292cd"/></svg>WHAT WE DO</h3>
        <p>Lorem ipsum dolor sit amet, consectetur adipiscing elit. Sed diam nonummy in convallis gravida lacus. Mauris metus accumsan, aliquam et eleifend. Sollicitudin sed massa vel enim eu. Curabitur tempus vehicula nisi ut porttitor in convallis.</p>
        <a class="btn" href="#">Read more</a>
      </article>
      <article class="feature">
        <h3><svg width="18" height="18" viewBox="0 0 20 20"><circle cx="10" cy="10" r="7" fill="none" stroke="#0292cd" stroke-width="2"/><path d="M6 10l3 3 5-6" fill="none" stroke="#0292cd" stroke-width="2"/></svg>OUR SERVICES</h3>
        <ul>
          <li>Commercial Security Systems</li>
          <li>Data &amp; Fibre Installation</li>
          <li>Information Communication &amp; Technology</li>
          <li>Electrical Fit-Out</li>
        </ul>
        <a class="btn" href="#">Read more</a>
      </article>
    </section>

    <section class="block welcome">
      <h2>Wecome to <span>BRTL.com</span></h2>
      <p>Lorem ipsum dolor sit amet, consectetur adipiscing elit. Sed diam nonummy in convallis gravida lacus. Mauris metus accumsan, aliquam et eleifend ut pretium. Sollicitudin sed massa vel enim eu lobortis. Curabitur tempus vehicula nisi ut porttitor in convallis. Aenean ultrices urna vel lorem aliquet, sit amet feugiat nibh posuere. Donec quis tortor id magna volutpat tempor. Integer sed dolor vitae arcu dictum molestie sit amet at elit. Proin eu velit nec turpis gravida pharetra quis a sapien vestibulum.</p>
      <a class="more" href="#">read more</a>
      <div class="welcome-photo" role="img" aria-label="Photo of a business professional in an office"></div>
    </section>

    <section class="block showcase">
      <div class="tabs"><span class="on">FEATURED</span><span>NEW ARRIVALS</span><span>ON SALE</span></div>
      <div class="tab-panel">
        <i class="thumb" role="img" aria-label="Project photo of data cabling" style="background:linear-gradient(135deg,#5b7f9a,#b8ccd9)"></i>
        <i class="thumb" role="img" aria-label="Project photo of network switches" style="background:linear-gradient(135deg,#3e6a8a,#9fc0d6)"></i>
        <i class="thumb" role="img" aria-label="Project photo of electrical panel" style="background:linear-gradient(135deg,#6c8494,#cfdbe3)"></i>
        <i class="thumb" role="img" aria-label="Project photo of fibre optic cables" style="background:linear-gradient(135deg,#2f6f9c,#8ac0e0)"></i>
        <i class="thumb" role="img" aria-label="Project photo of server room" style="background:linear-gradient(135deg,#4b5f72,#aebfcc)"></i>
      </div>
    </section>

    <section class="block about">
      <div class="about-copy">
        <h2>ABOUT US</h2>
        <p>Lorem ipsum dolor sit amet, consectetur adipiscing elit. Sed diam nonummy in convallis gravida lacus. Mauris metus accumsan, aliquam et eleifend ut pretium. Sollicitudin sed massa vel enim eu lobortis, curabitur tempus vehicula nisi.</p>
        <p>Lorem ipsum dolor sit amet, consectetur adipiscing elit. Sed diam nonummy in convallis gravida lacus. Mauris metus accumsan, aliquam et eleifend ut pretium vel enim eu lobortis.</p>
        <p>Lorem ipsum dolor sit amet, consectetur adipiscing elit. Sed diam nonummy in convallis gravida lacus. Mauris metus accumsan, aliquam et eleifend ut pretium. Sollicitudin sed massa vel enim eu lobortis, curabitur tempus vehicula nisi.</p>
        <a class="btn" href="#" style="margin-top:10px">Read more</a>
      </div>
      <aside class="news">
        <h4>LATEST NEWS &amp; EVENTS</h4>
        <div class="news-item"><i role="img" aria-label="News photo"></i><div><b>Lorem ipsum dolor sit amet, consectetur</b><span>Sed diam nonummy in convallis gravida lacus mauris</span></div></div>
        <div class="news-item"><i role="img" aria-label="News photo"></i><div><b>Lorem ipsum dolor sit amet, consectetur</b><span>Sed diam nonummy in convallis gravida lacus mauris</span></div></div>
        <div class="news-item"><i role="img" aria-label="News photo"></i><div><b>Lorem ipsum dolor sit amet, consectetur</b><span>Sed diam nonummy in convallis gravida lacus mauris</span></div></div>
        <div class="news-item"><i role="img" aria-label="News photo"></i><div><b>Lorem ipsum dolor sit amet, consectetur</b><span>Sed diam nonummy in convallis gravida lacus mauris</span></div></div>
        <div class="news-item"><i role="img" aria-label="News photo"></i><div><b>Lorem ipsum dolor sit amet, consectetur</b><span>Sed diam nonummy in convallis gravida lacus mauris</span></div></div>
        <a class="all" href="#">See All</a>
      </aside>
    </section>

    <section class="block partners">
      <h2 class="section-title">Our Partners</h2>
      <p class="section-sub">Lorem ipsum dolor sit amet, consectetur adipiscing elit. Sed diam nonummy in convallis gravida lacus.</p>
      <div class="partner-row"><i></i><i></i><i></i><i></i><i></i></div>
    </section>

    <section class="block testimonials">
      <h2>What Our Customer Says</h2>
      <div class="quotes">
        <div class="quote"><span class="avatar" role="img" aria-label="Customer portrait"></span><div><p>Lorem ipsum dolor sit amet, consectetur adipiscing elit. Sed diam nonummy in convallis gravida lacus, mauris metus accumsan aliquam et eleifend ut pretium.</p><cite><b>Mara Quill</b>, Marketing, Sydney</cite></div></div>
        <div class="quote"><span class="avatar" role="img" aria-label="Customer portrait"></span><div><p>Lorem ipsum dolor sit amet, consectetur adipiscing elit. Sed diam nonummy in convallis gravida lacus, mauris metus accumsan aliquam et eleifend ut pretium.</p><cite><b>Dane Holloway</b>, IT Manager, Brisbane</cite></div></div>
        <div class="quote"><span class="avatar" role="img" aria-label="Customer portrait"></span><div><p>Lorem ipsum dolor sit amet, consectetur adipiscing elit. Sed diam nonummy in convallis gravida lacus, mauris metus accumsan aliquam et eleifend ut pretium.</p><cite><b>Lena Ortis</b>, Project Manager, Perth</cite></div></div>
        <div class="quote"><span class="avatar" role="img" aria-label="Customer portrait"></span><div><p>Lorem ipsum dolor sit amet, consectetur adipiscing elit. Sed diam nonummy in convallis gravida lacus, mauris metus accumsan aliquam et eleifend ut pretium.</p><cite><b>Rui Calder</b>, CEO, Adelaide</cite></div></div>
      </div>
    </section>

    <footer class="block footer">
      <div class="footer-col"><h5>MAIN MENU</h5><ul><li>Home</li><li>About us</li><li>Services</li><li>ISP</li><li>Recent Projects</li><li>Blog</li><li>Contact Us</li></ul></div>
      <div class="footer-col split"><h5>USEFUL LINKS</h5><ul><li>Terms &amp; Conditions</li><li>Privacy Policy</li><li>Help</li><li>FAQs</li><li>Sitemap</li><li>Careers</li><li>Support</li><li>Downloads</li></ul></div>
      <div class="footer-col"><h5>GET IN TOUCH</h5><ul><li>BRTL Pty Ltd</li><li>12 Harbour Lane, Suite 4</li><li>Docklands VIC, Australia</li><li>Telephone: 1300 555 019</li><li>Fax: (03) 9555 0142</li><li>Email: info@brtlgroup.com.au</li></ul></div>
      <div class="footer-col"><h5>MY ACCOUNT</h5><ul><li>My Account</li><li>Login</li><li>Register</li><li>My Cart</li><li>My Wishlist</li></ul></div>
    </footer>

    <section class="block newsletter">
      <div class="newsletter-row">
        <h5>NEWSLETTER</h5>
        <div>
          <div class="newsletter-note">Receive Our News &amp; updates weekly, to learn about our latest work</div>
          <div style="display:flex;gap:6px;margin-top:4px"><span class="field">Your email address</span><a class="btn" href="#">SUBMIT</a></div>
        </div>
      </div>
      <div class="follow">FOLLOW US ON <i></i><i></i><i></i><i></i></div>
    </section>

    <div class="block copyright">Copyright © 2015 BRTL.com All rights reserved</div>

  </div>
</div>
</body>
</html>
```